PPE EQIUPMENT

WE WOULD LIKE TO PRODUCE 2 DIFFERENT BANNERS TO BE PLACED OUTSIDE OF OUR WAREHOUSE TO ADVERTISE THAT WE HAVE FACE MASKS, HAND SANITISERS, DISINFECTANT SPRAY, FACE SHIELDS AND HAND SOAP. THE SIZE OF EACH BANNER WILL BE , portrait to be (W) 140 cm x (H) 250 cm, with 4 x eyelets. THE BANNER IS TO STATE PPE EQUIPMENT AVAILABLE HERE AND SHOW OUR PHONE NUMBER 0208-417-2953. FINALLY WE WILL REQUIRE SOME IMAGES OF THE PRODUCTS IF YOU CAN SUPPLY THESE. THANKS

```html
<!DOCTYPE html>
<html lang="en">
<head>
<meta charset="utf-8">
<title>PPE Equipment Banner</title>
<link href="https://fonts.googleapis.com/css2?family=Anton&family=Archivo+Black&family=Arimo&family=Barlow:wght@300;500&family=Bebas+Neue&display=swap" rel="stylesheet">
<style>
  :root {
    --navy: #1f3a70;
    --ink: #333333;
    --paper: #ffffff;
    --backdrop: #d6d6d6;
    --tint: #e4eaf4;
  }
  * { margin: 0; padding: 0; box-sizing: border-box; }
  html, body { width: 960px; height: 1200px; overflow: hidden; background: var(--backdrop); }
  .banner {
    position: absolute; left: 162px; top: 30px;
    width: 636px; height: 1140px;
    background: var(--paper);
  }
  .headline {
    position: absolute; top: 58px; left: 0; width: 100%;
    text-align: center;
    font-family: "Anton", sans-serif;
    font-size: 90px; line-height: 1;
    color: var(--navy);
    letter-spacing: -1px;
  }
  .subline {
    position: absolute; top: 160px; left: 0; width: 100%;
    text-align: center;
    font-family: "Arimo", sans-serif;
    font-size: 50px; line-height: 1;
    color: var(--navy);
  }
  .phone-band {
    position: absolute; top: 222px; left: 0; width: 100%; height: 111px;
    background: var(--navy);
    display: flex; align-items: center; justify-content: center;
  }
  .phone-number {
    font-family: "Archivo Black", sans-serif;
    font-size: 64px; line-height: 1;
    color: var(--paper);
  }
  .product-list {
    position: absolute; top: 355px; left: 36px; right: 0;
    list-style: none;
  }
  .product {
    display: flex; align-items: center;
    height: 113px; margin-bottom: 6px;
  }
  .product-icon {
    width: 147px; height: 113px;
    border: 9px solid var(--navy);
    border-radius: 11px;
    flex: none;
    background: linear-gradient(160deg, var(--paper), var(--tint));
  }
  .product-name {
    margin-left: 18px;
    font-family: "Bebas Neue", sans-serif;
    font-size: 66px; line-height: 1;
    color: var(--ink);
    padding-top: 4px;
  }
  .brand-band {
    position: absolute; top: 972px; left: 0; width: 100%; height: 168px;
    background: var(--navy);
    text-align: center;
    color: var(--paper);
  }
  .brand-name {
    margin-top: 26px;
    font-family: "Barlow", sans-serif;
    font-weight: 500;
    font-size: 58px; line-height: 1;
    letter-spacing: 2px;
  }
  .brand-tagline {
    margin-top: 8px;
    font-family: "Barlow", sans-serif;
    font-weight: 300;
    font-size: 31px; line-height: 1;
    letter-spacing: 1.5px;
  }
</style>
</head>
<body>
  <main class="banner">
    <h1 class="headline">PPE EQUIPMENT</h1>
    <p class="subline">AVAILABLE HERE</p>
    <div class="phone-band"><p class="phone-number">0208-417-2953</p></div>
    <ul class="product-list">
      <li class="product"><div class="product-icon" role="img" aria-label="Face mask pictogram"></div><span class="product-name">FACE MASKS</span></li>
      <li class="product"><div class="product-icon" role="img" aria-label="Hand sanitiser pump bottle with hands pictogram"></div><span class="product-name">HAND SANITISERS</span></li>
      <li class="product"><div class="product-icon" role="img" aria-label="Disinfectant spray bottle pictogram"></div><span class="product-name">DISINFECTANT SPRAY</span></li>
      <li class="product"><div class="product-icon" role="img" aria-label="Face shield pictogram"></div><span class="product-name">FACE SHIELDS</span></li>
      <li class="product"><div class="product-icon" role="img" aria-label="Bar of soap on an open hand pictogram"></div><span class="product-name">HAND SOAP</span></li>
    </ul>
    <footer class="brand-band">
      <p class="brand-name">OAKLINE FURNITURE</p>
      <p class="brand-tagline">TRADE FURNITURE SOLUTIONS</p>
    </footer>
  </main>
</body>
</html>
```